Residential Remodeling Contractor needs updated business card

I need a new design for my business card.
Name of the company is Ridgefell Construction. I need a card that commands presence, strength, integrity. I have been in business for 28 years. I am a Residential Remodeling Contractor that covers all aspects of a residential remodel and build.

```html
<!DOCTYPE html>
<html lang="en">
<head>
<meta charset="utf-8">
<title>Ridgefell Construction – Business Card</title>
<link href="https://fonts.googleapis.com/css2?family=Open+Sans:wght@400;600;700&display=swap" rel="stylesheet">
<style>
  :root {
    --stage: #232323;
    --card-blue: #213d7c;
    --card-blue-deep: #1b3470;
    --ink-white: #ffffff;
    --rule: rgba(255, 255, 255, 0.55);
  }
  * { margin: 0; padding: 0; box-sizing: border-box; }
  html, body { width: 1200px; height: 780px; overflow: hidden; }
  body {
    background: var(--stage);
    font-family: "Open Sans", Arial, sans-serif;
    color: var(--ink-white);
    position: relative;
  }
  .card {
    position: absolute;
    top: 235px;
    width: 540px;
    height: 310px;
    background: var(--card-blue);
    overflow: hidden;
  }
  .card--front { left: 40px; }
  .card--back { left: 620px; background: var(--card-blue-deep); }

  /* Front */
  .brand {
    position: absolute;
    left: 34px;
    top: 82px;
    width: 200px;
    display: flex;
    align-items: center;
    gap: 10px;
  }
  .brand__square {
    width: 14px;
    height: 14px;
    background: var(--ink-white);
    flex: none;
  }
  .brand__name {
    font-weight: 600;
    font-size: 22px;
    line-height: 1.15;
    letter-spacing: 0.04em;
    text-transform: uppercase;
    color: var(--ink-white);
  }
  .divider {
    position: absolute;
    left: 262px;
    top: 30px;
    width: 1px;
    height: 170px;
    background: var(--rule);
  }
  .contact {
    position: absolute;
    left: 292px;
    top: 40px;
  }
  .contact__name {
    font-weight: 700;
    font-size: 25px;
    line-height: 1.1;
  }
  .contact__title {
    font-size: 12.5px;
    margin-top: 3px;
    letter-spacing: 0.02em;
  }
  .contact__list {
    list-style: none;
    margin-top: 22px;
    font-size: 12.5px;
    line-height: 1;
  }
  .contact__list li {
    display: flex;
    align-items: center;
    gap: 8px;
    margin-bottom: 8px;
  }
  .contact__list svg { width: 13px; height: 13px; flex: none; }
  .address-band {
    position: absolute;
    left: 0;
    top: 232px;
    width: 100%;
    height: 32px;
    background: var(--ink-white);
    color: var(--card-blue);
    font-size: 13.5px;
    display: flex;
    align-items: center;
    justify-content: center;
    letter-spacing: 0.01em;
  }

  /* Back */
  .back-brand {
    position: absolute;
    inset: 0;
    display: flex;
    align-items: center;
    justify-content: center;
    gap: 14px;
  }
  .back-brand__square {
    width: 22px;
    height: 22px;
    background: #2f58b0;
  }
  .back-brand__name {
    font-weight: 600;
    font-size: 34px;
    line-height: 1.1;
    letter-spacing: 0.05em;
    text-transform: uppercase;
    color: #2f58b0;
  }
</style>
</head>
<body>

  <section class="card card--front" aria-label="Business card front">
    <div class="brand">
      <span class="brand__square"></span>
      <span class="brand__name">Ridgefell<br>Construction</span>
    </div>

    <span class="divider"></span>

    <div class="contact">
      <p class="contact__name">Daniel Hovorka</p>
      <p class="contact__title">Managing Director</p>
      <ul class="contact__list">
        <li>
          <svg viewBox="0 0 16 16" aria-hidden="true"><path fill="#fff" d="M3.6 1.5l2.3 2.6-1.3 1.9c.8 1.9 2.5 3.6 4.4 4.4l1.9-1.3 2.6 2.3-1.4 2.3C7 13.4 2.6 9 1.3 3z"/></svg>
          <span>(817) 555-0148</span>
        </li>
        <li>
          <svg viewBox="0 0 16 16" aria-hidden="true"><rect x="1.5" y="3.5" width="13" height="9" fill="none" stroke="#fff" stroke-width="1.4"/><path d="M1.5 3.5L8 9l6.5-5.5" fill="none" stroke="#fff" stroke-width="1.4"/></svg>
          <span>info@ridgefellbuild.com</span>
        </li>
        <li>
          <svg viewBox="0 0 16 16" aria-hidden="true"><circle cx="8" cy="8" r="6.5" fill="none" stroke="#fff" stroke-width="1.4"/><ellipse cx="8" cy="8" rx="2.8" ry="6.5" fill="none" stroke="#fff" stroke-width="1.1"/><path d="M1.5 8h13" stroke="#fff" stroke-width="1.1"/></svg>
          <span>www.ridgefellbuild.com</span>
        </li>
      </ul>
    </div>

    <div class="address-band">4180 Cedar Ridge Dr. Suite 210 Fort Worth, TX 76109</div>
  </section>

  <section class="card card--back" aria-label="Business card back">
    <div class="back-brand">
      <span class="back-brand__square"></span>
      <span class="back-brand__name">Ridgefell<br>Construction</span>
    </div>
  </section>

</body>
</html>
```